Ward Compass Business Card Design*

We need a business card design for our company Ward Compass. Our company is specialized in providing online consulting services regarding medical institutions, hospitals and doctors. We work with patients worldwide looking to choose between healthcare providers. We have a website you may use as a reference, where we list doctors and clinics worldwide. So we target Medical providers as well as patients worldwide.
Target Market(s)
Medical Providers and patients around the world
Industry/Entity Type
Medical
Contact Information for Business Card
Salwa Kettani
CEO
+90 612 348 2175
info@wardcompass.example
www.wardcompass.example
14 Annakhil 7 H.R.B. Rabat, Morocco
Requirements
Must have
- Company logo/name on one full side, personal info and smaller logo and company name on the other side.
Nice to have
- Smart and elegant design

```html
<!DOCTYPE html>
<html lang="en">
<head>
<meta charset="utf-8">
<title>Ward Compass — Business Card</title>
<link href="https://fonts.googleapis.com/css2?family=Quicksand:wght@400;500;700&display=swap" rel="stylesheet">
<style>
  :root {
    --backdrop: #161718;
    --card-dark: #2d2e30;
    --card-blue: #1f4076;
    --brand-blue: #2a5db0;
    --ink-light: #b9bcc0;
    --ink-muted: #8e9196;
    --deboss: #112746;
    --disc-grey: #7d7f82;
  }
  * { box-sizing: border-box; margin: 0; padding: 0; }
  html, body { width: 1200px; height: 900px; overflow: hidden; }
  body {
    background: var(--backdrop);
    font-family: "Quicksand", sans-serif;
    position: relative;
  }
  .card {
    position: absolute;
    top: 298px;
    width: 530px;
    height: 303px;
    border-radius: 3px;
    box-shadow: 0 18px 40px rgba(0,0,0,.55);
    overflow: hidden;
  }
  .card--details { left: 50px; background: var(--card-dark); }
  .card--brand { left: 620px; background: var(--card-blue); }

  /* details side */
  .brand-lockup {
    position: absolute; left: 34px; top: 34px;
    display: flex; align-items: center; gap: 12px;
  }
  .brand-lockup__dot {
    width: 30px; height: 30px; border-radius: 50%;
    background: var(--brand-blue);
  }
  .brand-lockup__name {
    font-size: 21px; font-weight: 500; letter-spacing: 2px;
    color: var(--ink-light); text-transform: uppercase;
  }
  .person { position: absolute; left: 34px; top: 104px; }
  .person__name { font-size: 19px; font-weight: 500; color: var(--ink-light); }
  .person__first { color: var(--brand-blue); }
  .person__role { font-size: 13px; color: var(--ink-muted); margin-top: 2px; }
  .contact-list {
    position: absolute; left: 34px; top: 170px;
    list-style: none; font-size: 13px; color: var(--ink-muted);
  }
  .contact-list li { display: flex; align-items: center; gap: 10px; height: 22px; }
  .contact-list svg { width: 12px; height: 12px; fill: var(--brand-blue); flex: none; }
  .accent-disc {
    position: absolute; right: -40px; bottom: -60px;
    width: 230px; height: 230px; border-radius: 50%;
    border: 16px solid var(--brand-blue);
    opacity: .0;
  }

  /* brand side */
  .brand-disc {
    position: absolute; left: 70px; top: 76px;
    width: 150px; height: 150px; border-radius: 50%;
    background: var(--disc-grey);
    box-shadow: inset 0 2px 4px rgba(0,0,0,.35);
  }
  .brand-wordmark {
    position: absolute; left: 250px; top: 136px;
    font-size: 26px; font-weight: 700; letter-spacing: 2px;
    color: var(--deboss); text-transform: uppercase;
    text-shadow: 0 1px 0 rgba(255,255,255,.08);
  }
</style>
</head>
<body>
  <section class="card card--details" aria-label="Business card, contact side">
    <div class="brand-lockup">
      <span class="brand-lockup__dot"></span>
      <span class="brand-lockup__name">Ward Compass</span>
    </div>
    <div class="person">
      <p class="person__name"><span class="person__first">Salwa</span> Kettani</p>
      <p class="person__role">CEO</p>
    </div>
    <ul class="contact-list">
      <li><svg viewBox="0 0 12 12" aria-hidden="true"><path d="M2.5 0.8 4.3 3 3.3 4.3c.7 1.7 2.2 3.2 4.4 4.4L9 7.7l2.2 1.8-1.1 1.9C5.6 11 1 6.4.6 1.9z"/></svg>+90 612 348 2175</li>
      <li><svg viewBox="0 0 12 12" aria-hidden="true"><path d="M0 2h12v8H0zM1 3l5 3.5L11 3v-.2H1z" fill-rule="evenodd"/></svg>info@wardcompass.example</li>
      <li><svg viewBox="0 0 12 12" aria-hidden="true"><path d="M6 0a6 6 0 1 0 0 12A6 6 0 0 0 6 0zm0 1.5c.8 1 1.3 2.6 1.4 3.8H4.6C4.7 4.1 5.2 2.5 6 1.5zM4.6 6.7h2.8c-.1 1.2-.6 2.8-1.4 3.8-.8-1-1.3-2.6-1.4-3.8z" fill-rule="evenodd"/></svg>www.wardcompass.example</li>
      <li><svg viewBox="0 0 12 12" aria-hidden="true"><path d="M6 0a4 4 0 0 0-4 4c0 3 4 8 4 8s4-5 4-8a4 4 0 0 0-4-4zm0 2.5a1.5 1.5 0 1 1 0 3 1.5 1.5 0 0 1 0-3z" fill-rule="evenodd"/></svg>14 Annakhil 7 H.R.B. Rabat, Morocco</li>
    </ul>
  </section>

  <section class="card card--brand" aria-label="Business card, brand side">
    <span class="brand-disc"></span>
    <p class="brand-wordmark">Ward Compass</p>
  </section>
</body>
</html>
```